" Somos uma empresa de assessoria e consultoria em gestão da qualidade e segurança dos alimentos. Nossa equipe é formada por engenheiros de alimentos. E a prestação de serviço realizada pela Vintora compreende: a) Auditorias diagnósticas dos sistemas de qualidade e segurança dos alimentos, ou seja, avaliação do status atual do cliente, de acordo com a legislação sanitária (órgãos de vigilância sanitária, como por ex. PROTEVA e Fundação Ribeiral Dastro) ou de acordo com as exigências de com normas reconhecidas internacionalmente, pelo setor alimentício, como por exemplo NRT 71500, Norte ROC; b) Auditorias de conformidade dos sistemas de qualidade e segurança dos alimentos, ou seja, avaliação do status do cliente, após correção das não conformidades apontadas na auditoria diagnóstica, de acordo com a legislação sanitária (órgãos de vigilância sanitária, como por ex. PROTEVA e Fundação Ribeiral Dastro) ou de acordo com as exigências de com normas reconhecidas internacionalmente, pelo setor alimentício, como por exemplo NRT 71500, Norte ROC; c) Auditorias Internas dos Sistemas de Qualidade e Segurança de limentos, onde é verificado a implementação e manutenção dos Sistemas de Qualidade e Segurança dos Alimentos; d) Elaboração de documentos referentes à qualidade e segurança de alimentos, exigidos pela legislação sanitária em vigor no Brasil e/ou legislação sanitária de outros países e/ou àquelas exigidas por normas internacionais; e) Implantação de Sistemas de Qualidade e Segurança dos Alimentos, de acordo com a legislação sanAitária em vigor no Brasil e/ou legislação sanitária de outros países e/ou normas internacionais; f) Capacitação de profissionais de nível gerencial ou de supervisão, assim como também manipuladores de alimentos diretos ou indiretos, em temas relacionados à qualidade e segurança dos alimentos; g) Comercio eletrônico (atividade futura) de produtos relacionados à sistema de qualidade e segurança dos alimentos, como por exemplo: instrumentos de medição (termômetros, por exemplo), equipamentos de proteção individual (EPIs), sinalizadores educativos, entre outros. O método utilizado para a comercialização será por meio de representação de fabricantes destes produtos. "

```html
<!DOCTYPE html>
<html lang="pt-BR">
<head>
<meta charset="UTF-8">
<title>Vintora – Cartão de visita</title>
<link rel="stylesheet" href="https://fonts.googleapis.com/css2?family=Arimo:ital,wght@0,400;0,700;1,700&display=swap">
<style>
  :root {
    --bg: #e9e9ea;
    --card: #ffffff;
    --ink: #2b2b2d;
    --ink-soft: #4a4a4d;
    --red: #d0202a;
    --charcoal: #2f3033;
    --rule: #9a9a9c;
  }
  * { box-sizing: border-box; margin: 0; padding: 0; }
  html, body {
    width: 1200px; height: 1200px; overflow: hidden;
    background: var(--bg);
    font-family: "Arimo", Arial, sans-serif;
    color: var(--ink);
  }
  .canvas {
    width: 1200px; height: 1200px;
    display: flex; flex-direction: column; align-items: center; justify-content: center;
    gap: 60px;
  }
  .card {
    position: relative;
    width: 880px; height: 500px;
    background: var(--card);
    box-shadow: 0 10px 30px rgba(0,0,0,.12);
    overflow: hidden;
  }
  .card-edge { position: absolute; left: 0; bottom: 0; width: 100%; height: 70px; display: block; }

  /* Front */
  .brand {
    position: absolute; left: 150px; top: 150px;
    display: flex; flex-direction: column; align-items: flex-start;
  }
  .brand-row { display: flex; align-items: center; gap: 22px; }
  .brand-dot { width: 64px; height: 64px; border-radius: 50%; background: var(--red); }
  .brand-name {
    font-weight: 700; font-size: 108px; letter-spacing: 4px; line-height: 1;
    color: var(--ink);
  }
  .brand-tagline {
    margin-top: 14px; margin-left: 86px;
    font-weight: 700; font-style: italic; font-size: 25px;
    color: var(--red);
  }

  /* Back */
  .contact {
    position: absolute; left: 70px; top: 58px; right: 60px;
  }
  .contact-head { display: flex; align-items: flex-start; gap: 28px; }
  .person-name { font-weight: 700; font-size: 36px; color: var(--ink); }
  .person-role {
    margin-top: 4px; padding-top: 6px; border-top: 2px solid var(--rule);
    font-size: 19px; letter-spacing: 1px; color: var(--ink-soft);
    display: inline-block; padding-right: 30px;
  }
  .contact-list { list-style: none; margin-top: 30px; }
  .contact-item {
    display: flex; align-items: flex-start; gap: 30px;
    font-size: 19px; color: var(--ink-soft); margin-bottom: 24px; line-height: 1.35;
  }
  .icon { width: 26px; height: 26px; flex: 0 0 26px; display: block; }
</style>
</head>
<body>
<main class="canvas">

  <section class="card card-front" aria-label="Frente do cartão">
    <div class="brand">
      <div class="brand-row">
        <span class="brand-dot"></span>
        <span class="brand-name">VINTORA</span>
      </div>
      <p class="brand-tagline">Excelência em segurança dos alimentos!</p>
    </div>
    <svg class="card-edge" viewBox="0 0 880 70" preserveAspectRatio="none" aria-hidden="true">
      <path d="M0 62 L560 62 L560 70 L0 70 Z" fill="var(--red)"/>
      <path d="M560 70 L600 22 Q606 14 618 14 L880 14 L880 70 Z" fill="var(--charcoal)"/>
    </svg>
  </section>

  <section class="card card-back" aria-label="Verso do cartão">
    <div class="contact">
      <div class="contact-head">
        <svg class="icon" viewBox="0 0 26 26" aria-hidden="true">
          <circle cx="13" cy="9" r="6" fill="var(--ink)"/>
          <path d="M2 26 Q2 15 13 15 Q24 15 24 26 Z" fill="var(--ink)"/>
        </svg>
        <div>
          <h1 class="person-name">Marina Lopes Vieira</h1>
          <p class="person-role">DIRETORA EXECUTIVA</p>
        </div>
      </div>
      <ul class="contact-list">
        <li class="contact-item">
          <svg class="icon" viewBox="0 0 26 26" aria-hidden="true">
            <circle cx="13" cy="13" r="12" fill="var(--ink)"/>
            <g fill="none" stroke="#fff" stroke-width="1.5">
              <ellipse cx="13" cy="13" rx="5" ry="10"/>
              <line x1="3" y1="13" x2="23" y2="13"/>
              <line x1="13" y1="3" x2="13" y2="23"/>
            </g>
          </svg>
          <span>www.vintoraconsultoria.com.br</span>
        </li>
        <li class="contact-item">
          <svg class="icon" viewBox="0 0 26 26" aria-hidden="true">
            <circle cx="13" cy="13" r="12" fill="var(--ink)"/>
            <path d="M8 7 L11 7 L12 10 L10.5 11.5 Q12 15 14.5 15.5 L16 14 L19 15 L19 18 Q18 19 16 19 Q8 18 7 9 Q7 7.5 8 7 Z" fill="#fff"/>
          </svg>
          <span>+55 11 94371-5820</span>
        </li>
        <li class="contact-item">
          <svg class="icon" viewBox="0 0 26 26" aria-hidden="true">
            <rect x="1" y="5" width="24" height="16" rx="2" fill="var(--ink)"/>
            <path d="M2 6 L13 14 L24 6" fill="none" stroke="#fff" stroke-width="1.6"/>
          </svg>
          <span>marina@vintoraconsultoria.com.br</span>
        </li>
        <li class="contact-item">
          <svg class="icon" viewBox="0 0 26 26" aria-hidden="true">
            <path d="M13 1 Q22 1 22 10 Q22 16 13 25 Q4 16 4 10 Q4 1 13 1 Z" fill="var(--ink)"/>
            <circle cx="13" cy="10" r="3.5" fill="#fff"/>
          </svg>
          <span>Rua das Acácias 742 - CJ 58 - Edifício Solaris - Vila Aurora<br>CEP 04512-090 - São Paulo - SP</span>
        </li>
      </ul>
    </div>
    <svg class="card-edge" viewBox="0 0 880 70" preserveAspectRatio="none" aria-hidden="true">
      <rect x="0" y="40" width="880" height="3" fill="var(--rule)"/>
      <rect x="0" y="48" width="880" height="22" fill="var(--red)"/>
    </svg>
  </section>

</main>
</body>
</html>
```